Request for Business Card Design

Hi. My name is Marlene, I am looking for a new business card design for my company, Quarrow Signal Instruments, LLC. I really like the design you did for Tarsel Venture and was hoping you could do something similar using our full logo and our mark. I am also open to any raised texture design using our mark. I have attached our full logo, which would need to be somewhere on the card, as well as the mark in both outline and full form, as well as our brand colors / guide. The card does not have to be white, as long as our logo and mark appear. I actually like darker colored business cards more, but am open to all options. If you are interested in working with me, please let me know. We would also take the business card design into letterhead design if you can do that.

```html
<!DOCTYPE html>
<html lang="en">
<head>
<meta charset="UTF-8">
<title>Quarrow Signal Instruments — Business Card</title>
<link href="https://fonts.googleapis.com/css2?family=Lato:wght@400;700;900&display=swap" rel="stylesheet">
<style>
  :root {
    --backdrop: #2b2b2b;
    --card: #1c1c1d;
    --brand-blue: #0299c4;
    --silver: #b9b9bb;
    --ink-light: #f2f2f2;
  }
  * { margin: 0; padding: 0; box-sizing: border-box; }
  html, body {
    width: 1200px; height: 875px; overflow: hidden;
    background: var(--backdrop);
    font-family: "Lato", Arial, sans-serif;
  }
  .stage { position: relative; width: 1200px; height: 875px; }

  .card {
    position: absolute;
    width: 560px; height: 320px;
    background: var(--card);
    overflow: hidden;
  }

  /* Front face: pill-rounded left edge */
  .card--front {
    left: 70px; top: 90px;
    border-radius: 160px 18px 18px 160px;
    display: flex; align-items: center;
    padding-left: 90px;
  }
  .brand-lockup { display: flex; align-items: center; gap: 22px; }
  .brand-dot {
    width: 58px; height: 58px; border-radius: 50%;
    background: var(--brand-blue);
    flex-shrink: 0;
  }
  .brand-name {
    font-weight: 900; font-size: 34px; line-height: 1.05;
    letter-spacing: 2px; text-transform: uppercase;
    color: var(--silver);
  }

  /* Back face: contact details */
  .card--back {
    left: 570px; top: 465px;
    border-radius: 18px;
  }
  .back-brand {
    position: absolute; right: 34px; top: 34px;
    display: flex; align-items: center; gap: 12px;
  }
  .back-brand__dot {
    width: 30px; height: 30px; border-radius: 50%;
    background: var(--brand-blue); flex-shrink: 0;
  }
  .back-brand__name {
    font-weight: 900; font-size: 16px; line-height: 1.1;
    letter-spacing: 1.5px; text-transform: uppercase;
    color: var(--brand-blue);
  }
  .contact {
    position: absolute; left: 40px; bottom: 32px;
    color: var(--ink-light);
  }
  .contact__name {
    font-weight: 900; font-size: 40px; letter-spacing: 2px;
    text-transform: uppercase; color: var(--brand-blue); line-height: 1;
  }
  .contact__title { font-size: 17px; font-weight: 700; margin: 4px 0 12px; }
  .contact__list { list-style: none; font-size: 13.5px; line-height: 1.55; }
  .contact__list li { display: flex; align-items: center; gap: 9px; }
  .contact__list svg { width: 12px; height: 12px; fill: var(--brand-blue); flex-shrink: 0; }
  .contact__company {
    margin-top: 8px; font-size: 15px; font-weight: 700; color: var(--brand-blue);
  }
  .contact__address { font-size: 13px; }
</style>
</head>
<body>
<main class="stage">

  <section class="card card--front" aria-label="Business card front">
    <div class="brand-lockup">
      <span class="brand-dot" aria-hidden="true"></span>
      <span class="brand-name">Quarrow Signal<br>Instruments</span>
    </div>
  </section>

  <section class="card card--back" aria-label="Business card back">
    <div class="back-brand">
      <span class="back-brand__dot" aria-hidden="true"></span>
      <span class="back-brand__name">Quarrow Signal<br>Instruments</span>
    </div>
    <div class="contact">
      <h1 class="contact__name">Marlene</h1>
      <p class="contact__title">Founder &amp; CEO</p>
      <ul class="contact__list">
        <li>
          <svg viewBox="0 0 24 24" aria-hidden="true"><path d="M6.6 10.8a15.5 15.5 0 0 0 6.6 6.6l2.2-2.2a1 1 0 0 1 1-.25 11.4 11.4 0 0 0 3.6.57 1 1 0 0 1 1 1V20a1 1 0 0 1-1 1A17 17 0 0 1 3 4a1 1 0 0 1 1-1h3.5a1 1 0 0 1 1 1c0 1.25.2 2.450.57 3.57a1 1 0 0 1-.25 1z"/></svg>
          +001 720 555 0148
        </li>
        <li>
          <svg viewBox="0 0 24 24" aria-hidden="true"><path d="M6 2h12v6H6zM4 9h16a2 2 0 0 1 2 2v6h-4v5H6v-5H2v-6a2 2 0 0 1 2-2zm4 8v3h8v-3z"/></svg>
          +001 720 555 0193
        </li>
        <li>
          <svg viewBox="0 0 24 24" aria-hidden="true"><path d="M2 5h20v14H2zm2 2v.5l8 5 8-5V7l-8 5z"/></svg>
          marlene@quarrowsignal.com
        </li>
        <li>
          <svg viewBox="0 0 24 24" aria-hidden="true"><path d="M12 2a10 10 0 1 0 0 20 10 10 0 0 0 0-20zm6.9 9h-3a15 15 0 0 0-1.4-6 8 8 0 0 1 4.4 6zM12 4.1A13 13 0 0 1 13.9 11h-3.8A13 13 0 0 1 12 4.1zM9.5 5a15 15 0 0 0-1.4 6h-3a8 8 0 0 1 4.4-6zM5.1 13h3a15 15 0 0 0 1.4 6 8 8 0 0 1-4.4-6zm6.9 6.9A13 13 0 0 1 10.1 13h3.8A13 13 0 0 1 12 19.9zm2.5-.9a15 15 0 0 0 1.4-6h3a8 8 0 0 1-4.4 6z"/></svg>
          quarrowsignal.com
        </li>
      </ul>
      <p class="contact__company">Quarrow Signal Instruments, LLC</p>
      <p class="contact__address">1180 Fieldstone Parkway, Ridgemont, CO 80412</p>
    </div>
  </section>

</main>
</body>
</html>
```